Business Card Design for BrightvaleMedia.com

--I need a business card design for my company BrightvaleMedia.com

I have attached my logo...I want the brightvale media logo on the front of the business card, and then I want The Quillstone Chief on the back of it with my information.

I would like to see a light colored background as well as a dark colored background

FRONT:
BRIGHTVALE MEDIA LOGO
248 N. Larkmoor
3rd Floor
San Diego CA 92173
www.BrightvaleMedia.com

Advanced Website & App Development
Websites, Apps, Online Voucher Systems

Leading Edge Marketing Services
SMS, VB, SMM, SEM,

BACK:
QUILLSTONE CHIEF LOGO
Dorian Pelletta
The Quillstone Chief
Call Or Text: 619-555-0148
Dorian@QuillstoneChief.example
www.QuillstoneChief.example

Target Market(s)

small business owners

Industry/Entity Type

Business Consultant

Contact Information for Business Card

FRONT:
BRIGHTVALE MEDIA LOGO
248 N. Larkmoor
3rd Floor
San Diego CA 92173
www.BrightvaleMedia.com

SMS, VB, SMM, SEM,

BACK:
QUILLSTONE CHIEF LOGO
Dorian Pelletta
The Quillstone Chief
Dorian@QuillstoneChief.example
www.QuillstoneChief.example

Requirements
Must have
• add this quote on it somewhere, anywhere,preferrably on back
• "The Fastest Way To Success Is To Take Action”
• — Dorian Pelletta, Quillstone Chief
Nice to have
• open
Should not have
• red

```html
<!DOCTYPE html>
<html lang="en">
<head>
<meta charset="utf-8">
<title>Brightvale Media – Business Card</title>
<link href="https://fonts.googleapis.com/css2?family=PT+Sans:ital,wght@0,400;0,700;1,400&display=swap" rel="stylesheet">
<style>
  :root {
    --stage: #000000;
    --card-grey: #6d6e71;
    --card-blue: #0072a8;
    --accent-blue: #2a8fd0;
    --ink-light: #ffffff;
    --ink-soft: #e6e7e8;
  }
  * { margin: 0; padding: 0; box-sizing: border-box; }
  html, body { width: 1200px; height: 900px; overflow: hidden; background: var(--stage); }
  body { font-family: "PT Sans", Arial, sans-serif; color: var(--ink-light); position: relative; }

  .card { position: absolute; top: 275px; width: 477px; height: 293px; }
  .card--back { left: 116px; background: var(--card-grey); border-radius: 0 46px 0 46px; }
  .card--front { left: 622px; background: var(--card-blue); border-radius: 46px 0 46px 0; }

  .wordmark { position: absolute; font-weight: 700; white-space: nowrap; line-height: 1; }
  .card--back .wordmark { left: 42px; top: 54px; font-size: 26px; letter-spacing: 2px; color: var(--accent-blue); }
  .card--front .wordmark { right: 44px; top: 50px; font-size: 27px; letter-spacing: 2px; color: var(--ink-light); }

  .person { position: absolute; right: 20px; top: 143px; text-align: right; }
  .person__name { font-size: 16px; font-weight: 700; line-height: 20px; }
  .person__title { font-size: 14px; line-height: 18px; }

  .contact-list { position: absolute; right: 18px; top: 201px; list-style: none; text-align: right; }
  .contact-list li { font-size: 14px; line-height: 17px; display: flex; justify-content: flex-end; align-items: center; gap: 8px; }
  .contact-list svg { width: 10px; height: 10px; fill: var(--ink-light); flex: none; }

  .quote { position: absolute; left: 42px; top: 198px; width: 190px; }
  .quote__text { font-size: 13px; font-style: italic; line-height: 17px; color: var(--ink-light); }
  .quote__author { margin-top: 5px; font-size: 11px; line-height: 14px; color: var(--ink-soft); }

  .company-info { position: absolute; left: 23px; top: 119px; font-size: 14px; line-height: 17px; }
  .company-info .address { margin-bottom: 4px; }
  .company-info .web { margin-bottom: 10px; }
  .services-main { font-size: 11.5px; font-weight: 700; line-height: 15px; text-transform: uppercase; margin-bottom: 14px; }
  .services-more { font-size: 14px; line-height: 17px; }
</style>
</head>
<body>

<section class="card card--back" aria-label="Card back">
  <div class="wordmark">QUILLSTONE CHIEF</div>
  <div class="person">
    <p class="person__name">Dorian Pelletta</p>
    <p class="person__title">The Quillstone Chief</p>
  </div>
  <blockquote class="quote">
    <p class="quote__text">“The Fastest Way To Success Is To Take Action”</p>
    <p class="quote__author">— Dorian Pelletta, Quillstone Chief</p>
  </blockquote>
  <ul class="contact-list">
    <li>619-555-0148
      <svg viewBox="0 0 10 10" aria-hidden="true"><path d="M2 0.5 L3.6 2.6 L2.8 3.6 C3.4 5 4.8 6.5 6.3 7.2 L7.4 6.3 L9.5 7.9 L8.6 9.5 C4.5 9.3 0.7 5.5 0.5 1.4 Z"/></svg>
    </li>
    <li>Dorian@QuillstoneChief.example
      <svg viewBox="0 0 10 10" aria-hidden="true"><path d="M0.5 2.2 H9.5 V2.9 L5 5.8 L0.5 2.9 Z M0.5 3.9 L5 6.8 L9.5 3.9 V8 H0.5 Z"/></svg>
    </li>
    <li>www.QuillstoneChief.example
      <svg viewBox="0 0 10 10" aria-hidden="true"><circle cx="5" cy="5" r="4.5"/><path d="M0.6 5 H9.4 M5 0.6 V9.4" stroke="#6d6e71" stroke-width="0.8"/></svg>
    </li>
  </ul>
</section>

<section class="card card--front" aria-label="Card front">
  <div class="wordmark">BRIGHTVALE MEDIA</div>
  <div class="company-info">
    <p class="address">248 N. Larkmoor<br>3rd Floor, San Diego CA 92173</p>
    <p class="web">www.BrightvaleMedia.com</p>
    <p class="services-main">Advanced Website &amp; App Development<br>Websites, Apps, Online Voucher Systems</p>
    <p class="services-more">Leading Edge Marketing Services<br>SMS | VB | SMM | SEM,</p>
  </div>
</section>

</body>
</html>
```